PostCard Design Project

I am making a mailing postcard
I am having the mailing printed using 4 color foil on certain parts.
I am looking for a design that maximizes the foil process where certain parts are done in foil to grab the customers attention (example: if there is a car on the postcard the headlights would be done in foil) .
I am targeting some industries, (auto, real estate, medical, beauty) I would like the post card to have examples of postcard ideas for 2 or 3 of these industries.
specs:
the postcard should be atleast 6.5x9 up to 8.5x11, I don't want to restrict the space for the creative as I don't want everything to look like a huge mess. both sides will be used.
the piece is a direct mail piece so it has to meet requirements of https://www.mailvantor.com/business/pdf/quick-reference-guide.pdf
text will be
"business with no limits, meet mailing with no addresses, gain new customers through "Open Porch Route Drop" reach new customers at their home without needing their address. "
I also want some current print specials I am running included.
-double your order FREE (order 500 business cards and get 1000)
-250 100lb gloss stock brochures 99.00
-business packages (cards, envelopes and letterhead) 299
-1000 flyers 140.40
-5000 postcards 179.99
A list of services
banners
booklets
brochures
business cards
calendars
catalogs
CD/DVD packages
envelopes
event tickets
flyers
hangtags
postcards
posters
presentation folders
rack cards
labels
table tents
window cling and decal
"order 24/7 orders@inkwillow.com" must be included
my logo is InkWillow will be supplied later
ive received some great designs. however Im looking for something a little more modern like some zorvel would put out. if the amount of words is too much please feel free to edit. also an idea i had for the list of services i offer is to have it transparent yet readable as the background of the postcard some small some big but covering the entire backgroud. you can then design on top of that with other thing. just an early morning thought
Reason: I have uploaded a sketch of my idea, please take time to look at it for an accurate depiction of what im looking for. feel free to add elements that make it pop off the page
Reason: We are getting close i will be providing feed back today

```html
<!DOCTYPE html>
<html lang="en">
<head>
<meta charset="utf-8">
<title>InkWillow Postcard</title>
<link rel="stylesheet" href="https://fonts.googleapis.com/css2?family=Open+Sans:wght@400&family=Arimo:wght@400;700&display=swap">
<style>
  :root {
    --page: #e9e6e1;
    --navy: #1d3550;
    --navy-deep: #13243a;
    --navy-light: #2c4a68;
    --lime: #b5d531;
    --quote-lime: #c8e23c;
    --sky: #1ea8dc;
    --sky-pale: #8fd3ee;
    --ink: #161a1f;
    --black-panel: #0b0d10;
    --white: #ffffff;
    --contact: #e4e8ee;
  }
  * { margin: 0; padding: 0; box-sizing: border-box; }
  html, body {
    width: 1200px; height: 900px; overflow: hidden;
    background: var(--page);
  }
  .postcard {
    position: absolute; left: 50px; top: 20px;
    width: 1012px; height: 792px;
    transform: scale(1.087); transform-origin: 0 0;
    overflow: hidden;
    background: var(--navy);
    box-shadow: 0 6px 18px rgba(0,0,0,.25);
  }
  .postcard__backdrop { position: absolute; inset: 0; }
  .logo-placeholder {
    position: absolute; left: 381px; top: 36px; width: 500px;
    font-family: "Arimo", Arial, sans-serif; font-weight: 700;
    color: var(--white); font-size: 53px; line-height: 57px;
    text-align: center; letter-spacing: -0.5px;
  }
  .specials {
    position: absolute; left: 546px; top: 243px;
    list-style: none;
    font-family: "Open Sans", Calibri, sans-serif;
    color: var(--ink); font-size: 22px; line-height: 33px;
  }
  .specials li { position: relative; padding-left: 23px; white-space: nowrap; }
  .specials li::before {
    content: ""; position: absolute; left: 0; top: 12px;
    width: 10px; height: 10px; border-radius: 50%; background: var(--ink);
  }
  .specials__detail { display: block; }
  .tagline {
    position: absolute; left: 0; top: 577px; width: 1012px;
    font-family: "Arimo", Arial, sans-serif;
    color: var(--quote-lime); font-size: 32px; line-height: 37.5px;
    text-align: center; white-space: nowrap;
  }
  .contact {
    position: absolute; left: 0; top: 729px; width: 1012px;
    font-family: "Arimo", Arial, sans-serif;
    color: var(--contact); font-size: 28px; text-align: center;
  }
</style>
</head>
<body>
<main class="postcard">
  <svg class="postcard__backdrop" width="1012" height="792" viewBox="0 0 1012 792">
    <defs>
      <radialGradient id="sample-glow" cx="0.45" cy="0.4" r="0.65">
        <stop offset="0" stop-color="var(--sky-pale)"/>
        <stop offset="1" stop-color="var(--sky)"/>
      </radialGradient>
    </defs>
    <rect width="1012" height="792" fill="var(--navy)"/>
    <polygon points="560,0 760,0 600,175 400,175" fill="var(--navy-light)" opacity=".35"/>
    <polygon points="820,0 1012,0 1012,60 880,175 700,175" fill="var(--navy-light)" opacity=".25"/>
    <path d="M0,0 L120,0 Q45,35 0,115 Z" fill="var(--lime)"/>
    <rect x="0" y="175" width="1012" height="330" fill="var(--lime)"/>
    <rect x="0" y="505" width="1012" height="7" fill="var(--black-panel)"/>
    <rect x="0" y="512" width="1012" height="7" fill="var(--sky)"/>
    <rect x="0" y="519" width="1012" height="4" fill="var(--black-panel)"/>
    <rect x="0" y="523" width="1012" height="9" fill="var(--navy-deep)"/>
    <rect x="0" y="532" width="1012" height="165" fill="var(--black-panel)"/>
    <rect x="0" y="697" width="1012" height="95" fill="var(--navy)"/>
    <polygon points="0,697 180,697 90,792 0,792" fill="var(--navy-light)" opacity=".3"/>
    <polygon points="800,697 1012,697 1012,792 720,792" fill="var(--navy-light)" opacity=".3"/>
    <circle cx="242" cy="284" r="254" fill="var(--white)"/>
    <circle cx="242" cy="284" r="242" fill="var(--navy-deep)"/>
    <circle cx="242" cy="284" r="228" fill="var(--white)"/>
    <circle cx="242" cy="284" r="214" fill="url(#sample-glow)" role="img"
            aria-label="Fanned collage of printed samples: brochures, flyers, folded leaflets and business cards"/>
  </svg>

  <h1 class="logo-placeholder">YOUR LOGO<br>HERE</h1>

  <ul class="specials">
    <li>Double your order FREE<span class="specials__detail">(order 500 business cards and get 1000)</span></li>
    <li>250 100lb gloss stock brochures 99.00</li>
    <li>Business packages<span class="specials__detail">(cards, envelopes and letterhead) 299</span></li>
    <li>1000 flyers 140.40</li>
    <li>5000 postcards 179.99</li>
  </ul>

  <p class="tagline">“ Business with no limits, meet mailing with no addresses,<br>Gain new customers through "Open Porch Route Drop"<br>Reach new customers at their home without needing their address. ”</p>

  <p class="contact">Contact Us : order 24/7 orders@inkwillow.com</p>
</main>
</body>
</html>
```